Corvane Card

The logo is the Spanish flag colors I want a vibrant eye catching design with the yellow / red colors over either Navy or white background or black even ,
Would like a 2D feel to the logo with another lighter color logo under it look ,

Contact Information for Business Card

Corvane Flooring
Teodor Vashkin
Main Number
Cell Number
Fax Number

Website on the side of the card somewhere

Font styles to use
Sans Serif

Colors
ec1f27
ffc214

Requirements
Must have
• 2 logos feel one is bolder and the other one underneath very light

```html
<!DOCTYPE html>
<html lang="en">
<head>
<meta charset="utf-8">
<title>Corvane Flooring – Business Card</title>
<link rel="stylesheet" href="https://fonts.googleapis.com/css2?family=Arimo:wght@400;700&family=Krona+One&display=swap">
<style>
  :root {
    --page-bg: #9a9a9a;
    --card-bg: #353433;
    --brand-red: #ec1f27;
    --brand-yellow: #ffc214;
    --text-light: #f2f2f2;
    --rule: #6e6d6b;
    --mark-dark: #141414;
  }
  * { margin: 0; padding: 0; box-sizing: border-box; }
  html, body {
    width: 1093px;
    height: 1200px;
    overflow: hidden;
    background: var(--page-bg);
    font-family: "Arimo", Arial, sans-serif;
  }
  .card {
    position: absolute;
    left: 265px;
    width: 578px;
    height: 357px;
    background: var(--card-bg);
  }
  .card--front { top: 226px; }
  .card--back  { top: 620px; }

  .brand-lockup {
    position: absolute;
    display: flex;
    align-items: center;
    gap: 18px;
  }
  .brand-square { flex: none; }
  .brand-name {
    font-family: "Arimo", Arial, sans-serif;
    font-weight: 700;
    text-transform: uppercase;
    line-height: 1;
  }
  .brand-name span { display: block; }

  .card--front .brand-lockup { right: 26px; top: 76px; }
  .card--front .brand-square { width: 44px; height: 44px; background: var(--brand-yellow); }
  .card--front .brand-name { color: var(--brand-red); }
  .card--front .brand-name span:first-child { font-size: 30px; letter-spacing: 5px; }
  .card--front .brand-name span + span { margin-top: 7px; font-size: 20px; letter-spacing: 12px; }

  .holder-name {
    position: absolute;
    left: 33px;
    top: 209px;
    font-family: "Krona One", Arial, sans-serif;
    font-size: 18.5px;
    font-weight: 400;
    text-transform: uppercase;
    letter-spacing: 0.5px;
    white-space: nowrap;
  }
  .holder-name .first { color: var(--brand-red); margin-right: 10px; }
  .holder-name .last { color: var(--brand-yellow); }

  .divider {
    position: absolute;
    left: 36px;
    right: 34px;
    top: 244px;
    height: 1px;
    background: var(--rule);
  }

  .phones {
    position: absolute;
    left: 33px;
    top: 266px;
    list-style: none;
  }
  .phones li, .online li {
    display: flex;
    align-items: center;
    height: 21px;
    color: var(--text-light);
    font-size: 17px;
    white-space: nowrap;
  }
  .phones svg { width: 17px; height: 15px; margin-right: 4px; fill: var(--brand-red); }

  .online {
    position: absolute;
    right: 37px;
    top: 286px;
    list-style: none;
  }
  .online li { justify-content: flex-end; font-size: 16px; }
  .online svg { width: 14px; height: 14px; margin-left: 8px; fill: var(--brand-red); }
  .online .web { color: var(--brand-red); }
  .web .accent { color: var(--brand-yellow); }

  .card--back .brand-lockup { left: 111px; top: 150px; gap: 26px; }
  .card--back .brand-square { width: 46px; height: 46px; background: var(--mark-dark); }
  .card--back .brand-name { color: var(--mark-dark); }
  .card--back .brand-name span:first-child { font-size: 31px; letter-spacing: 8px; }
  .card--back .brand-name span + span { margin-top: 9px; font-size: 21px; letter-spacing: 15px; }
</style>
</head>
<body>
  <section class="card card--front" aria-label="Business card front">
    <div class="brand-lockup">
      <div class="brand-square" aria-hidden="true"></div>
      <h1 class="brand-name"><span>Corvane</span><span>Flooring</span></h1>
    </div>

    <h2 class="holder-name"><span class="first">Teodor</span><span class="last">Vashkin</span></h2>
    <div class="divider"></div>

    <ul class="phones">
      <li>
        <svg viewBox="0 0 17 15" aria-hidden="true"><path d="M1 4c0-2 3-3 7.5-3S16 2 16 4v1h-3.5V3.5h-8V5H1z"/><path d="M4 6h9l2 8H2z"/></svg>
        604 210 3357
      </li>
      <li>
        <svg viewBox="0 0 17 15" aria-hidden="true"><path d="M5 0h7a1 1 0 0 1 1 1v13a1 1 0 0 1-1 1H5a1 1 0 0 1-1-1V1a1 1 0 0 1 1-1zm1 2v9h5V2z"/></svg>
        778 320 9146
      </li>
      <li>
        <svg viewBox="0 0 17 15" aria-hidden="true"><path d="M4 0h9v4H4z"/><path d="M1 5h15v6h-2V9H3v2H1z"/><path d="M4 10h9v5H4z"/></svg>
        604 210 3358
      </li>
    </ul>

    <ul class="online">
      <li>hello@corvane.com
        <svg viewBox="0 0 14 14" aria-hidden="true"><path d="M0 2h14v10H0zm1.5 1.5L7 8l5.5-4.5v-.2H1.5z"/></svg>
      </li>
      <li class="web">www.<span class="accent">corvanefloors</span>.com
        <svg viewBox="0 0 14 14" aria-hidden="true"><circle cx="7" cy="7" r="7"/><path d="M4 3c2 1 1 3 3 3s1 3 3 4" stroke="#fff" stroke-width="1.2" fill="none"/></svg>
      </li>
    </ul>
  </section>

  <section class="card card--back" aria-label="Business card back">
    <div class="brand-lockup">
      <div class="brand-square" aria-hidden="true"></div>
      <h2 class="brand-name"><span>Corvane</span><span>Flooring</span></h2>
    </div>
  </section>
</body>
</html>
```